Working Capital graphics

Our business advisory firm requires 9 images to be re-created and improved in the branding of our business.

The 9 images have been uploaded below and the colours and branding of the business can be found at the website www.tallowmereadvisory.com.au

```html
<!DOCTYPE html>
<html lang="en">
<head>
<meta charset="utf-8">
<title>Working Capital Cycles</title>
<link rel="stylesheet" href="https://fonts.googleapis.com/css2?family=Play:wght@700&display=swap">
<style>
  :root {
    --navy: #123a85;
    --sky: #0cb0f0;
    --orange: #f7941d;
    --white: #ffffff;
    --frame: #d6d6d6;
  }
  html, body { margin: 0; padding: 0; overflow: hidden; background: var(--white); }
  .canvas {
    width: 1200px; height: 1166px; box-sizing: border-box;
    border: 4px solid var(--frame); background: var(--white);
  }
  svg { display: block; font-family: "Play", sans-serif; font-variant-ligatures: none; font-feature-settings: normal; text-transform: none; }
  .hub-core { fill: var(--sky); }
  .hub-ring { fill: none; stroke: var(--navy); stroke-width: 2.5; }
  .spoke { stroke: var(--navy); stroke-width: 2.5; }
  .node { fill: var(--white); stroke: var(--orange); stroke-width: 3; }
  .node-label { fill: var(--navy); font-weight: 700; font-size: 8.5px; letter-spacing: .4px; text-anchor: middle; }
  .node-label.lg { font-size: 10px; }
  .hub-label { fill: var(--white); font-weight: 700; font-size: 21px; letter-spacing: 1px; text-anchor: middle; }
  .pill { fill: var(--navy); }
  .pill-label { fill: var(--white); font-weight: 700; font-size: 18px; letter-spacing: 1px; text-anchor: middle; }
  .wedge { fill: var(--orange); }
  .divider { stroke: var(--white); stroke-width: 2; fill: none; }
  .wedge-label { fill: var(--white); font-weight: 700; font-size: 20px; letter-spacing: 1.5px; text-anchor: middle; }
  .arrow-shaft { stroke: var(--navy); stroke-width: 4; }
  .arrow-head { fill: var(--navy); }
</style>
</head>
<body>
<div class="canvas">
<svg width="1192" height="1158" viewBox="4 4 1192 1158" aria-label="Working capital cycles: customer to cash, forecast to fulfillment, purchase to pay">

  <g class="cycle revenue">
    <g transform="translate(265 268)">
      <g class="spokes">
        <line class="spoke" x1="0" y1="-96" x2="0" y2="-116"/>
        <line class="spoke" x1="0" y1="-96" x2="0" y2="-116" transform="rotate(30)"/>
        <line class="spoke" x1="0" y1="-96" x2="0" y2="-116" transform="rotate(60)"/>
        <line class="spoke" x1="0" y1="-96" x2="0" y2="-116" transform="rotate(90)"/>
        <line class="spoke" x1="0" y1="-96" x2="0" y2="-116" transform="rotate(120)"/>
        <line class="spoke" x1="0" y1="-96" x2="0" y2="-116" transform="rotate(150)"/>
        <line class="spoke" x1="0" y1="-96" x2="0" y2="-116" transform="rotate(180)"/>
        <line class="spoke" x1="0" y1="-96" x2="0" y2="-116" transform="rotate(210)"/>
        <line class="spoke" x1="0" y1="-96" x2="0" y2="-116" transform="rotate(240)"/>
        <line class="spoke" x1="0" y1="-96" x2="0" y2="-116" transform="rotate(270)"/>
        <line class="spoke" x1="0" y1="-96" x2="0" y2="-116" transform="rotate(300)"/>
        <line class="spoke" x1="0" y1="-96" x2="0" y2="-116" transform="rotate(330)"/>
      </g>
      <circle class="hub-ring" r="96"/>
      <circle class="hub-core" r="87"/>
      <text class="hub-label" y="-4">REVENUE</text>
      <text class="hub-label" y="20">MANAGEMENT</text>
    </g>
    <circle class="node" cx="265" cy="118" r="34"/><text class="node-label lg" x="265" y="115">CUSTOMER<tspan x="265" dy="11">STRATEGY</tspan></text>
    <circle class="node" cx="340" cy="138" r="34"/><text class="node-label" x="340" y="136">SALES<tspan x="340" dy="10">MANAGEMENT</tspan></text>
    <circle class="node" cx="395" cy="193" r="34"/><text class="node-label" x="395" y="191">RISK<tspan x="395" dy="10">MANAGEMENT</tspan></text>
    <circle class="node" cx="416" cy="268" r="34"/><text class="node-label" x="416" y="266">CONTRACT<tspan x="416" dy="10">MANAGEMENT</tspan></text>
    <circle class="node" cx="395" cy="343" r="34"/><text class="node-label" x="395" y="341">SALES ORDER<tspan x="395" dy="10">PROCESSING</tspan></text>
    <circle class="node" cx="340" cy="398" r="34"/><text class="node-label lg" x="340" y="395">CREDIT<tspan x="340" dy="11">CHECK</tspan></text>
    <circle class="node" cx="266" cy="419" r="34"/><text class="node-label" x="266" y="417">ORDER<tspan x="266" dy="10">FULFILLMENT</tspan></text>
    <circle class="node" cx="190" cy="398" r="34"/><text class="node-label lg" x="190" y="401">BILLING</text>
    <circle class="node" cx="135" cy="344" r="34"/><text class="node-label lg" x="135" y="341">CUSTOMER<tspan x="135" dy="11">SERVICE</tspan></text>
    <circle class="node" cx="115" cy="269" r="34"/><text class="node-label lg" x="115" y="266">CASH<tspan x="115" dy="11">COLLECTION</tspan></text>
    <circle class="node" cx="135" cy="194" r="34"/><text class="node-label" x="135" y="187">RECEIPT &amp;<tspan x="135" dy="10">ALLOCATION</tspan><tspan x="135" dy="10">OF CASH</tspan></text>
    <circle class="node" cx="190" cy="139" r="34"/><text class="node-label" x="190" y="137">CASH<tspan x="190" dy="10">MANAGEMENT</tspan></text>
    <rect class="pill" x="157" y="501" width="218" height="36" rx="18"/>
    <text class="pill-label" x="266" y="525" textLength="178" lengthAdjust="spacingAndGlyphs">CUSTOMER TO CASH</text>
  </g>

  <g class="cycle supply">
    <g transform="translate(928 272)">
      <g class="spokes">
        <line class="spoke" x1="0" y1="-97" x2="0" y2="-122"/>
        <line class="spoke" x1="0" y1="-97" x2="0" y2="-122" transform="rotate(36)"/>
        <line class="spoke" x1="0" y1="-97" x2="0" y2="-122" transform="rotate(72)"/>
        <line class="spoke" x1="0" y1="-97" x2="0" y2="-122" transform="rotate(108)"/>
        <line class="spoke" x1="0" y1="-97" x2="0" y2="-122" transform="rotate(144)"/>
        <line class="spoke" x1="0" y1="-97" x2="0" y2="-122" transform="rotate(180)"/>
        <line class="spoke" x1="0" y1="-97" x2="0" y2="-122" transform="rotate(216)"/>
        <line class="spoke" x1="0" y1="-97" x2="0" y2="-122" transform="rotate(252)"/>
        <line class="spoke" x1="0" y1="-97" x2="0" y2="-122" transform="rotate(288)"/>
        <line class="spoke" x1="0" y1="-97" x2="0" y2="-122" transform="rotate(324)"/>
      </g>
      <circle class="hub-ring" r="97"/>
      <circle class="hub-core" r="88"/>
      <text class="hub-label" y="-4">SUPPLY CHAIN</text>
      <text class="hub-label" y="20">MANAGEMENT</text>
    </g>
    <circle class="node" cx="928" cy="111" r="39"/><text class="node-label lg" x="928" y="101">SUPPLY<tspan x="928" dy="13">CHAIN</tspan><tspan x="928" dy="13">STRATEGY</tspan></text>
    <circle class="node" cx="1020" cy="141" r="39"/><text class="node-label" x="1020" y="131">PRODUCT<tspan x="1020" dy="10">RANGE</tspan><tspan x="1020" dy="10">MANAGEMENT</tspan></text>
    <circle class="node" cx="1077" cy="218" r="39"/><text class="node-label" x="1077" y="221">FORECASTING</text>
    <circle class="node" cx="1078" cy="315" r="39"/><text class="node-label" x="1078" y="313">SALES ORDER<tspan x="1078" dy="11">FORECASTING</tspan></text>
    <circle class="node" cx="1022" cy="394" r="39"/><text class="node-label lg" x="1022" y="391">PRODUCTION<tspan x="1022" dy="11">SCHEDULING</tspan></text>
    <circle class="node" cx="931" cy="425" r="39"/><text class="node-label lg" x="931" y="414">RAW<tspan x="931" dy="13">MATERIAL</tspan><tspan x="931" dy="13">PLANNING</tspan></text>
    <circle class="node" cx="839" cy="397" r="39"/><text class="node-label lg" x="839" y="394">PRODUCTION<tspan x="839" dy="11">PLANNING</tspan></text>
    <circle class="node" cx="780" cy="321" r="39"/><text class="node-label" x="780" y="324">PRODUCTION</text>
    <circle class="node" cx="777" cy="224" r="39"/><text class="node-label" x="777" y="227">WAREHOUSING</text>
    <circle class="node" cx="832" cy="144" r="39"/><text class="node-label" x="832" y="147">DISTRIBUTION</text>
    <rect class="pill" x="797" y="500" width="264" height="36" rx="18"/>
    <text class="pill-label" x="929" y="524" textLength="234" lengthAdjust="spacingAndGlyphs">FORECAST TO FULFILLMENT</text>
  </g>

  <g class="capital-triangle">
    <polygon class="wedge" points="600,350 409,541 790,541"/>
    <path class="divider" d="M600 350 V463 M409 541 L600 463 L790 541"/>
    <text class="wedge-label" transform="translate(558 446) rotate(-45)">A/R</text>
    <text class="wedge-label" transform="translate(665 444) rotate(45)">INVENTORY</text>
    <text class="wedge-label" x="599" y="516">A/P</text>
  </g>

  <g class="arrows">
    <line class="arrow-shaft" x1="502" y1="427" x2="478" y2="404"/>
    <polygon class="arrow-head" points="470,396 494,402 476,414"/>
    <line class="arrow-shaft" x1="706" y1="427" x2="730" y2="404"/>
    <polygon class="arrow-head" points="738,396 732,420 720,402"/>
    <line class="arrow-shaft" x1="607" y1="557" x2="607" y2="590"/>
    <polygon class="arrow-head" points="607,601 596,580 607,586 618,580"/>
  </g>

  <g class="cycle expenditure">
    <g transform="translate(600 835)">
      <g class="spokes">
        <line class="spoke" x1="0" y1="-97" x2="0" y2="-122"/>
        <line class="spoke" x1="0" y1="-97" x2="0" y2="-122" transform="rotate(36)"/>
        <line class="spoke" x1="0" y1="-97" x2="0" y2="-122" transform="rotate(72)"/>
        <line class="spoke" x1="0" y1="-97" x2="0" y2="-122" transform="rotate(108)"/>
        <line class="spoke" x1="0" y1="-97" x2="0" y2="-122" transform="rotate(144)"/>
        <line class="spoke" x1="0" y1="-97" x2="0" y2="-122" transform="rotate(180)"/>
        <line class="spoke" x1="0" y1="-97" x2="0" y2="-122" transform="rotate(216)"/>
        <line class="spoke" x1="0" y1="-97" x2="0" y2="-122" transform="rotate(252)"/>
        <line class="spoke" x1="0" y1="-97" x2="0" y2="-122" transform="rotate(288)"/>
        <line class="spoke" x1="0" y1="-97" x2="0" y2="-122" transform="rotate(324)"/>
      </g>
      <circle class="hub-ring" r="97"/>
      <circle class="hub-core" r="88"/>
      <text class="hub-label" y="-4">EXPENDITURE</text>
      <text class="hub-label" y="20">MANAGEMENT</text>
    </g>
    <circle class="node" cx="600" cy="674" r="39"/><text class="node-label" x="600" y="672">PURCHASING<tspan x="600" dy="11">STRATEGY</tspan></text>
    <circle class="node" cx="692" cy="704" r="39"/><text class="node-label" x="692" y="702">BUDGETING &amp;<tspan x="692" dy="11">FORECASTING</tspan></text>
    <circle class="node" cx="748" cy="782" r="39"/><text class="node-label" x="748" y="780">ORIGINATING<tspan x="748" dy="11">REQUIREMENTS</tspan></text>
    <circle class="node" cx="749" cy="878" r="39"/><text class="node-label" x="749" y="876">SELECTING &amp;<tspan x="749" dy="11">NEGOTIATING</tspan></text>
    <circle class="node" cx="693" cy="958" r="39"/><text class="node-label" x="693" y="956">ORDERING &amp;<tspan x="693" dy="11">CONTRACTING</tspan></text>
    <circle class="node" cx="602" cy="988" r="39"/><text class="node-label" x="602" y="986">RECEIVING &amp;<tspan x="602" dy="11">EVALUATING</tspan></text>
    <circle class="node" cx="510" cy="960" r="39"/><text class="node-label" x="510" y="958">DISCREPANCY<tspan x="510" dy="11">MANAGEMENT</tspan></text>
    <circle class="node" cx="451" cy="883" r="39"/><text class="node-label lg" x="451" y="881">INVOICE<tspan x="451" dy="11">PROCESSING</tspan></text>
    <circle class="node" cx="449" cy="787" r="39"/><text class="node-label lg" x="449" y="785">PAYMENT<tspan x="449" dy="11">ISSUANCE</tspan></text>
    <circle class="node" cx="502" cy="707" r="39"/><text class="node-label" x="502" y="705">CASH<tspan x="502" dy="11">MANAGEMENT</tspan></text>
    <rect class="pill" x="490" y="1066" width="218" height="36" rx="18"/>
    <text class="pill-label" x="599" y="1090" textLength="162" lengthAdjust="spacingAndGlyphs">PURCHASE TO PAY</text>
  </g>
</svg>
</div>
</body>
</html>
```